Re-style home page - eye-catching and unique design for social commerce website

We need a new concept design for BrinoKet's home page.
We don't want to make huge changes but creating a more professional and eye-catching style.

We need to look very serious like a professional services company and in the same time to look like a social network for e-commerce.

Our logo is very captive and you can use to creating something of harmonious.

This is a re-style and I'm excepted to see unique and fresh design like Glimmora.

Target Market(s)

e-commerce and social

Industry/Entity Type

Social

Number of Pages Required

1 page

Font styles to use
Serif
Sans Serif

Requirements
Must have
• An eye-catching result.
• Search bar with logo and Login How it works and business
• The slogan with login and signup.
• Footer links.
Nice to have
• I would like to open the home page and see only two clear ways:
• -Consumer
• --Search
• --The slogan
• --Login and Signup
• --How it works
• -Business
• --Go to Business area
• Background: City, Shopping.
Should not have
• Scrollbar style!

```html
<!DOCTYPE html>
<html lang="en">
<head>
<meta charset="utf-8">
<title>BrinoKet — Shop Directly From Your Profile</title>
<link rel="stylesheet" href="https://fonts.googleapis.com/css2?family=Open+Sans:wght@400;600;700&display=swap">
<style>
  :root {
    --ink: #ffffff;
    --header-bg: rgba(8, 8, 8, 0.88);
    --nav-text: #c9c9c9;
    --chip-bg: rgba(28, 28, 28, 0.86);
    --chip-tick: #9a9a9a;
    --social-blue: #2f4d8f;
    --social-blue-dark: #253e76;
    --footer-bg: #ffffff;
    --footer-text: #6a6a6a;
    --login-bg-top: #fbfbfb;
    --login-bg-bottom: #d9d9d9;
    --login-text: #333333;
  }
  * { box-sizing: border-box; margin: 0; padding: 0; }
  html, body { width: 1200px; height: 801px; overflow: hidden; }
  body {
    font-family: "Open Sans", Arial, sans-serif;
    color: var(--ink);
    position: relative;
    background: #1b1a19;
  }
  .backdrop {
    position: absolute; inset: 0 0 40px 0;
    background:
      radial-gradient(ellipse at 50% 40%, rgba(90, 82, 72, 0.55) 0%, rgba(20, 18, 16, 0) 60%),
      linear-gradient(180deg, #2a2724 0%, #3a352f 45%, #2c2824 75%, #3b3733 100%);
  }
  .site-header {
    position: absolute; top: 0; left: 0; width: 1200px; height: 80px;
    background: var(--header-bg);
  }
  .brand {
    position: absolute; left: 113px; top: 19px;
    display: flex; align-items: center; gap: 10px;
    font-weight: 700; font-size: 36px; letter-spacing: -0.5px; color: var(--ink);
  }
  .brand-dot { width: 26px; height: 26px; border-radius: 50%; background: #ffffff; }
  .search {
    position: absolute; left: 339px; top: 22px; width: 370px; height: 37px;
    border: 0; background: #fff; padding: 0 11px;
    font-family: inherit; font-size: 13px; color: #999;
  }
  .search::placeholder { color: #8f8f8f; }
  .main-nav {
    position: absolute; left: 726px; top: 30px;
    display: flex; align-items: center; font-size: 14.5px; line-height: 20px;
    color: var(--nav-text); white-space: nowrap;
  }
  .main-nav .sep { margin: 0 11px; }
  .signup {
    position: absolute; left: 984px; top: 23px; width: 107px; height: 35px;
    border: 1px solid #8a8a8a; border-radius: 2px;
    display: flex; align-items: center; justify-content: center;
    font-size: 14.5px; color: var(--nav-text); white-space: nowrap;
  }
  .headline {
    position: absolute; top: 134px; width: 100%; text-align: center;
    font-size: 32px; font-weight: 600;
  }
  .feed-panel {
    position: absolute; left: 247px; top: 226px; width: 706px; height: 456px;
    border-radius: 4px; overflow: hidden;
  }
  .feed-photo {
    position: absolute; inset: 0;
    background: linear-gradient(100deg, #d9cfc3 0%, #b7a493 30%, #d2b9a4 50%, #c9b09c 70%, #e6ddd2 100%);
  }
  .badge {
    position: absolute; left: 568px; top: 196px; width: 64px; height: 64px;
    border-radius: 50%; background: #2a2a2a; border: 3px solid #555;
  }
  .panel-login {
    position: absolute; right: 16px; top: 15px; width: 90px; height: 36px;
    background: linear-gradient(var(--login-bg-top), var(--login-bg-bottom));
    border-radius: 2px; box-shadow: 0 2px 4px rgba(0,0,0,0.3);
    color: var(--login-text); font-size: 18px; font-weight: 600;
    display: flex; align-items: center; justify-content: center;
  }
  .feed-title {
    position: absolute; top: 42px; width: 100%; text-align: center;
    font-size: 32px; line-height: 42px; font-weight: 600; text-shadow: 0 2px 6px rgba(0,0,0,0.45);
  }
  .categories {
    position: absolute; left: 12px; top: 107px; width: 694px;
    display: flex; flex-direction: column; gap: 11px;
  }
  .category-row { display: flex; gap: 7px; list-style: none; }
  .chip {
    height: 37px; background: var(--chip-bg); border-radius: 2px;
    display: flex; align-items: center; gap: 8px; padding: 0 11px 0 7px;
    font-size: 15.5px; letter-spacing: -0.1px; white-space: nowrap;
  }
  .chip svg { width: 17px; height: 17px; flex: none; }
  .tagline {
    position: absolute; top: 351px; width: 100%; text-align: center;
    font-size: 22px; line-height: 30px; font-weight: 600; text-shadow: 0 1px 4px rgba(0,0,0,0.4);
  }
  .social-login {
    position: absolute; left: 242px; top: 391px; width: 222px; height: 40px;
    background: var(--social-blue); border-radius: 2px;
    display: flex; align-items: center; font-size: 16px; white-space: nowrap;
  }
  .social-login .mark {
    width: 28px; height: 28px; margin: 0 18px 0 8px; background: var(--social-blue-dark);
    border: 1px solid rgba(255,255,255,0.5); flex: none;
  }
  .site-footer {
    position: absolute; left: 0; top: 761px; width: 1200px; height: 40px;
    background: var(--footer-bg); box-shadow: 0 -2px 4px rgba(0,0,0,0.35);
    display: flex; justify-content: center; align-items: center; gap: 21px;
    font-size: 14.5px; color: var(--footer-text);
  }
</style>
</head>
<body>
  <svg width="0" height="0" style="position:absolute">
    <symbol id="tick" viewBox="0 0 17 17">
      <circle cx="8.5" cy="8.5" r="8.5" fill="#9a9a9a"/>
      <path d="M4.5 8.8l2.8 2.7 5.2-5.6" stroke="#222" stroke-width="2" fill="none"/>
    </symbol>
  </svg>

  <div class="backdrop" role="img" aria-label="Blurred interior of a shopping mall arcade with shop fronts"></div>

  <header class="site-header">
    <div class="brand"><span>BrinoKet</span><span class="brand-dot"></span></div>
    <input class="search" type="text" placeholder="Search here...">
    <nav class="main-nav">
      <span>How It Works</span><span class="sep">|</span>
      <span>Business</span><span class="sep">|</span>
      <span>Login</span>
    </nav>
    <div class="signup">Sign Up Now</div>
  </header>

  <h1 class="headline">Shop Directly From Your Profile</h1>

  <section class="feed-panel">
    <div class="feed-photo" role="img" aria-label="Photo of two friends walking with shopping bags"></div>
    <div class="panel-login">LOGIN</div>
    <h2 class="feed-title">Setup Your Feed</h2>
    <div class="categories">
      <ul class="category-row">
        <li class="chip"><svg><use href="#tick"/></svg>Active Life</li>
        <li class="chip"><svg><use href="#tick"/></svg>Education</li>
        <li class="chip"><svg><use href="#tick"/></svg>Health &amp; Medical</li>
        <li class="chip"><svg><use href="#tick"/></svg>Public Services &amp; Government</li>
      </ul>
      <ul class="category-row">
        <li class="chip"><svg><use href="#tick"/></svg>Art &amp; Entertainment</li>
        <li class="chip"><svg><use href="#tick"/></svg>Event Planning &amp; Services</li>
        <li class="chip"><svg><use href="#tick"/></svg>Home Services</li>
        <li class="chip"><svg><use href="#tick"/></svg>Pets</li>
      </ul>
      <ul class="category-row">
        <li class="chip"><svg><use href="#tick"/></svg>Automative</li>
        <li class="chip"><svg><use href="#tick"/></svg>Financial Services</li>
        <li class="chip"><svg><use href="#tick"/></svg>Hotels</li>
        <li class="chip"><svg><use href="#tick"/></svg>Professional Services</li>
      </ul>
      <ul class="category-row">
        <li class="chip"><svg><use href="#tick"/></svg>Beauty &amp; Spas</li>
        <li class="chip"><svg><use href="#tick"/></svg>Local Services</li>
        <li class="chip"><svg><use href="#tick"/></svg>Mass Media</li>
        <li class="chip"><svg><use href="#tick"/></svg>Nighlife</li>
        <li class="chip"><svg><use href="#tick"/></svg>Food</li>
      </ul>
      <ul class="category-row">
        <li class="chip"><svg><use href="#tick"/></svg>Real Estate</li>
        <li class="chip"><svg><use href="#tick"/></svg>Restaurants</li>
        <li class="chip"><svg><use href="#tick"/></svg>Shopping</li>
      </ul>
    </div>
    <p class="tagline">Save your time. Live Better.</p>
    <div class="social-login"><span class="mark"></span>Login With Circlebook</div>
  </section>
  <div class="badge"></div>

  <footer class="site-footer">
    <span>About Us</span><span>Blog</span><span>Business</span><span>Jobs</span>
    <span>Privacy</span><span>FAQ</span><span>Contacts</span>
  </footer>
</body>
</html>
```